Logo, Web and Mobile Designs for enterprise social media platform

All the details are in the attached document, please start reading the scope document first which explains what is this project about and the details about the needed deliverables, after that please read the UI_Requirements document which will detail what is expected regarding the coded web version since this is a coded contest, it is very important that you meet the UI requirements or suggest something else but we will need to agree first before working on the coded version

Good Luck

Target Market(s)

Enterprise Social Media

Industry/Entity Type

Media

Coding

Coded - Design and coding required

Number of Pages Required

5+ page

Font styles to use
Sans Serif

Requirements
Must have
• All the must haves are listed in the scope document so please check before you start

```html
<!DOCTYPE html>
<html lang="en">
<head>
<meta charset="utf-8">
<title>Teamvora</title>
<link rel="stylesheet" href="https://fonts.googleapis.com/css2?family=Open+Sans:wght@300;400;600;700;800&family=Roboto:wght@300;400&family=Raleway:wght@400&display=swap">
<style>
  :root {
    --bar-dark: #444444;
    --bar-line: #d9d9d9;
    --nav-text: #e4e4e4;
    --white: #ffffff;
    --ink: #222222;
    --body-text: #666666;
    --label-text: #555555;
    --arrow-grey: #b3b3b3;
    --hero-deep: #3f8fb5;
    --hero-mid: #9cc9de;
    --hero-light: #e8eff5;
    --dot: #ffffff;
    --social-one: #3d5fa8;
    --social-two: #1aa6e4;
    --social-three: #e8502a;
  }
  * { margin: 0; padding: 0; box-sizing: border-box; }
  html, body { width: 1200px; height: 938px; overflow: hidden; background: var(--white); }
  body { position: relative; font-family: "Open Sans", Arial, sans-serif; }

  .site-header {
    position: absolute; left: 0; top: 0; width: 1200px; height: 65px;
    background: var(--bar-dark);
  }
  .brand {
    position: absolute; left: 151px; top: 14px;
    font-family: "Raleway", "Open Sans", sans-serif; font-weight: 400;
    font-size: 28px; color: var(--white); letter-spacing: 0.5px;
  }
  .main-nav { position: absolute; top: 23px; left: 0; width: 1200px; }
  .main-nav a {
    position: absolute; color: var(--nav-text); text-decoration: none;
    font-size: 13.5px; font-weight: 400; white-space: nowrap;
  }
  .nav-home { left: 801px; }
  .nav-about { left: 881px; }
  .nav-contact { left: 982px; }

  .hero {
    position: absolute; left: 0; top: 65px; width: 1200px; height: 574px;
    background:
      radial-gradient(ellipse at 75% 40%, rgba(240,244,250,0.9) 0%, rgba(240,244,250,0) 55%),
      radial-gradient(ellipse at 15% 80%, rgba(40,90,120,0.55) 0%, rgba(40,90,120,0) 45%),
      linear-gradient(110deg, var(--hero-mid) 0%, var(--hero-deep) 35%, var(--hero-light) 60%, #d8dde8 100%);
  }
  .hero-title {
    position: absolute; left: 155px; top: 215px; color: var(--white);
    text-shadow: 0 1px 4px rgba(0,0,0,0.25);
  }
  .hero-title .lead { display: block; font-size: 43px; font-weight: 400; line-height: 52px; }
  .hero-title .name { display: block; font-size: 49px; font-weight: 800; line-height: 56px; letter-spacing: 1px; }
  .slider-dots { position: absolute; top: 524px; left: 520px; width: 160px; height: 14px; }

  .events { position: absolute; left: 151px; top: 639px; width: 899px; height: 231px; }
  .events-title { position: absolute; left: 0; top: 22px; font-size: 28px; font-weight: 300; color: var(--ink); }
  .events-arrows { position: absolute; right: 0; top: 32px; }
  .event { position: absolute; top: 75px; width: 250px; }
  .event-one { left: 15px; }
  .event-two { left: 316px; }
  .event-three { left: 632px; width: 270px; }
  .event-mark { position: absolute; left: 0; top: 5px; }
  .event h3 { margin-left: 20px; font-size: 15px; font-weight: 700; color: var(--ink); white-space: nowrap; }
  .event p {
    margin-left: 20px; margin-top: 12px; font-family: "Roboto", Arial, sans-serif;
    font-weight: 300; font-size: 13.5px; line-height: 20.5px; color: var(--body-text);
  }
  .read-more {
    position: absolute; top: 115px; left: 20px; font-size: 11.5px; font-weight: 700;
    letter-spacing: 1.6px; color: var(--label-text); text-decoration: none; white-space: nowrap;
  }
  .read-more svg { margin-left: 6px; vertical-align: 1px; }

  .site-footer {
    position: absolute; left: 0; top: 870px; width: 1200px; height: 68px;
    background: var(--bar-dark); border-top: 3px solid var(--bar-line);
  }
  .copyright { position: absolute; left: 151px; top: 24px; font-size: 13px; color: var(--nav-text); }
  .follow { position: absolute; left: 857px; top: 24px; font-size: 13px; color: var(--nav-text); }
  .social { position: absolute; left: 943px; top: 18px; }
</style>
</head>
<body>
  <header class="site-header">
    <div class="brand">Teamvora</div>
    <nav class="main-nav">
      <a class="nav-home" href="#">Home</a>
      <a class="nav-about" href="#">About Us</a>
      <a class="nav-contact" href="#">Contact Us</a>
    </nav>
  </header>

  <section class="hero" role="img" aria-label="Photo of three colleagues smiling in a bright blue-toned office meeting">
    <h1 class="hero-title"><span class="lead">Welcome to</span><span class="name">TEAMVORA</span></h1>
    <svg class="slider-dots" width="160" height="14" viewBox="0 0 160 14" aria-hidden="true">
      <circle cx="6" cy="7" r="6" fill="var(--dot)"/>
      <circle cx="43" cy="7" r="6" fill="none" stroke="var(--dot)" stroke-width="1.6"/>
      <circle cx="80" cy="7" r="6" fill="var(--dot)"/>
      <circle cx="117" cy="7" r="6" fill="var(--dot)"/>
      <circle cx="154" cy="7" r="6" fill="var(--dot)"/>
    </svg>
  </section>

  <section class="events">
    <h2 class="events-title">Events</h2>
    <svg class="events-arrows" width="42" height="18" viewBox="0 0 42 18" aria-hidden="true">
      <circle cx="9" cy="9" r="9" fill="var(--arrow-grey)"/>
      <path d="M11 5 L7 9 L11 13" fill="none" stroke="#fff" stroke-width="2"/>
      <circle cx="33" cy="9" r="9" fill="var(--arrow-grey)"/>
      <path d="M31 5 L35 9 L31 13" fill="none" stroke="#fff" stroke-width="2"/>
    </svg>

    <article class="event event-one">
      <svg class="event-mark" width="11" height="10" viewBox="0 0 11 10" aria-hidden="true"><path d="M1 1 L5 5 L1 9 M6 1 L10 5 L6 9" fill="none" stroke="var(--ink)" stroke-width="1.4"/></svg>
      <h3>At vero eos et accusamus et</h3>
      <p>But I must explain to you how all this mistaken idea of denouncing pleasure and praising pain.</p>
      <a class="read-more" href="#">READ MORE<svg width="4" height="7" viewBox="0 0 4 7"><path d="M0 0 L4 3.5 L0 7Z" fill="var(--label-text)"/></svg></a>
    </article>

    <article class="event event-two">
      <svg class="event-mark" width="11" height="10" viewBox="0 0 11 10" aria-hidden="true"><path d="M1 1 L5 5 L1 9 M6 1 L10 5 L6 9" fill="none" stroke="var(--ink)" stroke-width="1.4"/></svg>
      <h3>On the other hand, we denounc</h3>
      <p>These cases are perfectly simple and easy to distinguish. In a free hour, when our power of choice is untrammelled.</p>
      <a class="read-more" href="#">READ MORE<svg width="4" height="7" viewBox="0 0 4 7"><path d="M0 0 L4 3.5 L0 7Z" fill="var(--label-text)"/></svg></a>
    </article>

    <article class="event event-three">
      <svg class="event-mark" width="11" height="10" viewBox="0 0 11 10" aria-hidden="true"><path d="M1 1 L5 5 L1 9 M6 1 L10 5 L6 9" fill="none" stroke="var(--ink)" stroke-width="1.4"/></svg>
      <h3>Owing to the claims of duty</h3>
      <p>these matters to this principle of selection: he rejects pleasures to secure other greater pleasures.</p>
      <a class="read-more" href="#">READ MORE<svg width="4" height="7" viewBox="0 0 4 7"><path d="M0 0 L4 3.5 L0 7Z" fill="var(--label-text)"/></svg></a>
    </article>
  </section>

  <footer class="site-footer">
    <div class="copyright">Copyrights @ 2015 All Rights Reserved</div>
    <div class="follow">Follow us on</div>
    <svg class="social" width="108" height="30" viewBox="0 0 108 30" role="img" aria-label="Social network links">
      <circle cx="15" cy="15" r="14.5" fill="var(--social-one)"/>
      <circle cx="52" cy="15" r="14.5" fill="var(--social-two)"/>
      <circle cx="92" cy="15" r="14.5" fill="var(--social-three)"/>
    </svg>
  </footer>
</body>
</html>
```